Party Favors and Decorations Business Needs A Business Card Design

We are in need of a Logo design and business card design for a new small business called Bright Lantern Designs. We create party decorations and favours for Bridal Showers, Baby Showers, Weddings Birthdays etc. This is a very personalized service based on Clients theme, colour, and style. We are looking for a high end elegant look. I have attached a file to the style I like including the type of paper.

Target Market(s)

women, young adults, expectant mothers, mothers

Industry/Entity Type

Small Business

Contact Information for Business Card

Bright Lantern Designs Essex, ON 519-847-2061 brightlanterndesigns.ca karen@brightlanterngiftbox.com find us on Chatterly

Logo Text

Bright Lantern Designs

Font styles to use
Script

Requirements
Must have
• Name, email, web address, phone number
Should not have
• cutesy graphics

```html
<!DOCTYPE html>
<html lang="en">
<head>
<meta charset="utf-8">
<title>Bright Lantern Designs – Business Card</title>
<link rel="stylesheet" href="https://fonts.googleapis.com/css2?family=Old+Standard+TT:wght@700&family=Arimo:wght@400;700&family=Parisienne&display=swap">
<style>
  :root {
    --backdrop: #e9e6e1;
    --card: #0b0b0b;
    --card-sheen: #1c1c1c;
    --ink: #ffffff;
    --ink-soft: #d9d9d9;
  }
  * { box-sizing: border-box; margin: 0; padding: 0; }
  html, body {
    width: 1200px; height: 892px; overflow: hidden;
    background: var(--backdrop);
  }
  .sheet {
    width: 1200px; height: 892px;
    display: flex; flex-direction: column;
    align-items: center; justify-content: center; gap: 32px;
  }
  .card {
    position: relative;
    width: 700px; height: 400px;
    background: linear-gradient(150deg, var(--card-sheen) 0%, var(--card) 45%, var(--card) 100%);
    color: var(--ink);
    box-shadow: 0 6px 18px rgba(0,0,0,0.25);
  }
  .wordmark {
    font-family: "Old Standard TT", Georgia, serif;
    font-weight: 700;
    color: var(--ink);
    line-height: 1.05;
  }
  /* Back side */
  .card--back { display: flex; align-items: center; justify-content: center; }
  .card--back .wordmark { font-size: 62px; text-align: center; }
  /* Front side */
  .card--front .wordmark {
    position: absolute; top: 46px; right: 56px;
    font-size: 40px; text-align: right;
  }
  .holder {
    position: absolute; top: 160px; right: 56px; text-align: right;
  }
  .holder__name {
    font-family: "Parisienne", cursive;
    font-size: 38px; color: var(--ink);
  }
  .holder__role {
    font-family: "Arimo", Arial, sans-serif;
    font-size: 14px; color: var(--ink-soft); margin-top: 2px;
  }
  .contact {
    position: absolute; left: 56px; bottom: 52px;
    font-family: "Arimo", Arial, sans-serif;
    font-size: 17px; line-height: 1.45; color: var(--ink);
    list-style: none;
  }
  .social {
    position: absolute; right: 56px; bottom: 52px;
    display: flex; align-items: center; gap: 10px;
    font-family: "Arimo", Arial, sans-serif; color: var(--ink);
  }
  .social__mark { width: 24px; height: 24px; background: var(--ink); border-radius: 3px; }
  .social__text { font-size: 16px; line-height: 1.1; }
  .social__lead { display: block; font-size: 10px; }
</style>
</head>
<body>
<main class="sheet">
  <section class="card card--back">
    <h1 class="wordmark">Bright Lantern Designs</h1>
  </section>

  <section class="card card--front">
    <p class="wordmark">Bright Lantern<br>Designs</p>
    <div class="holder">
      <p class="holder__name">Employee name</p>
      <p class="holder__role">Managing Director</p>
    </div>
    <ul class="contact">
      <li>519-847-2061</li>
      <li>www.brightlanterndesigns.ca</li>
      <li>karen@brightlanterngiftbox.com</li>
    </ul>
    <div class="social">
      <span class="social__mark"></span>
      <span class="social__text"><span class="social__lead">Find us on</span>Chatterly</span>
    </div>
  </section>
</main>
</body>
</html>
```